RWT Fittings Ltd Business Cards

We need a business card with our business logo. We provide window and door installations on high-rises in west coast British Colombia, Canada.

I would like my business information and details on one side of the card, and the other side the company name with logo

Target Market(s)

General Contractors

Industry/Entity Type

Construction

Contact Information for Business Card

one side i want my company name and logo in the dark theme logo that i provided

Requirements
Must have
• Marco Peltieri, 16045518293, RWTFittings@mailbox-demo.com, 1407-5194 Linden Row Burnaby BC, V5H 2K9, Owner & Manager

```html
<!DOCTYPE html>
<html lang="en">
<head>
<meta charset="utf-8">
<title>RWT Fittings Ltd Business Cards</title>
<link rel="stylesheet" href="https://fonts.googleapis.com/css2?family=Roboto:wght@400;700&display=swap">
<style>
  :root {
    --stage: #232323;
    --card-dark: #1f1f22;
    --brand-blue: #24a7e0;
    --band-grey: #9b9b9b;
    --ink-white: #ffffff;
    --ink-dark: #1b1b1d;
    --ink-soft: #d9d9d9;
  }
  * { margin: 0; padding: 0; box-sizing: border-box; }
  html, body { width: 1200px; height: 780px; overflow: hidden; background: var(--stage); }
  body { font-family: "Roboto", Arial, sans-serif; position: relative; }

  .card {
    position: absolute;
    width: 540px;
    height: 308px;
    top: 236px;
    border-radius: 3px;
    overflow: hidden;
  }
  .card--back { left: 50px; background: var(--card-dark); }
  .card--front { left: 610px; background: var(--brand-blue); }

  .brand {
    position: absolute;
    display: flex;
    align-items: center;
    gap: 12px;
    font-weight: 700;
    white-space: nowrap;
  }
  .brand__square { display: block; flex: none; }
  .card--back .brand { left: 196px; top: 62px; font-size: 30px; color: var(--brand-blue); }
  .card--back .brand__square { width: 26px; height: 26px; background: var(--brand-blue); }
  .card--front .brand { left: 50%; top: 50%; transform: translate(-50%, -50%); font-size: 40px; color: var(--ink-dark); }
  .card--front .brand__square { width: 34px; height: 34px; background: var(--ink-dark); }

  .name-band {
    position: absolute;
    left: 0; top: 132px;
    width: 232px; height: 76px;
    background: var(--band-grey);
    color: var(--ink-white);
    padding: 14px 0 0 30px;
  }
  .name-band__name { font-size: 24px; font-weight: 700; line-height: 1.1; }
  .name-band__role { font-size: 12px; font-weight: 400; margin-top: 4px; padding-left: 44px; }

  .address {
    position: absolute;
    left: 30px; top: 236px;
    font-size: 13px;
    color: var(--ink-white);
    white-space: nowrap;
  }

  .contact-band {
    position: absolute;
    left: 300px; top: 212px;
    width: 240px; height: 96px;
    background: var(--brand-blue);
    color: var(--ink-white);
    padding: 18px 0 0 16px;
    font-size: 13.5px;
  }
  .contact-band__row { display: flex; align-items: center; gap: 8px; margin-bottom: 9px; white-space: nowrap; }
  .contact-band__icon { width: 13px; height: 13px; flex: none; }
</style>
</head>
<body>

  <section class="card card--back" aria-label="Business card, contact side">
    <div class="brand">
      <span class="brand__square"></span>
      <span class="brand__name">RWT Fittings Ltd</span>
    </div>

    <div class="name-band">
      <p class="name-band__name">Marco Peltieri</p>
      <p class="name-band__role">Owner &amp; Manager</p>
    </div>

    <p class="address">1407-5194 Linden Row Burnaby BC, V5H 2K9</p>

    <div class="contact-band">
      <p class="contact-band__row">
        <svg class="contact-band__icon" viewBox="0 0 24 24" aria-hidden="true"><path fill="#fff" d="M6.6 10.8a15.1 15.1 0 0 0 6.6 6.6l2.2-2.2a1 1 0 0 1 1-.25 11.4 11.4 0 0 0 3.6.57 1 1 0 0 1 1 1V20a1 1 0 0 1-1 1A17 17 0 0 1 3 4a1 1 0 0 1 1-1h3.5a1 1 0 0 1 1 1c0 1.25.2 2.46.57 3.6a1 1 0 0 1-.25 1z"/></svg>
        <span>1604 551 8293</span>
      </p>
      <p class="contact-band__row">
        <svg class="contact-band__icon" viewBox="0 0 24 24" aria-hidden="true"><rect x="2" y="5" width="20" height="14" rx="2" fill="#fff"/><path d="M3 6l9 7 9-7" fill="none" stroke="#24a7e0" stroke-width="2"/></svg>
        <span>RWTFittings@mailbox-demo.com</span>
      </p>
    </div>
  </section>

  <section class="card card--front" aria-label="Business card, company side">
    <div class="brand">
      <span class="brand__square"></span>
      <span class="brand__name">RWT Fittings Ltd</span>
    </div>
  </section>

</body>
</html>
```